Toronto's Airline, based in Downtown looking for a whole new look and feel.

SkyMerrow is looking for a new look in our website. We are an airline based at Corwin Hale Airfield in Toronto. You can view our current website/services at www.skymerrow-example.com. We are expanding our services and look forward to a very sleek and modernized website. Please view the different pages on our website, we also need to add several new plane types as we have expanded and the website is not current. Would also be interesting to have a news feed or update feed through a widget which would be easy to use and update. we will also be implementing 2 third party programs called tavlo and quenbrook on the website, both are tour based and airline based sales and management functions.

Target Market(s)

Commuters, travel, tourism, dates, general public

Industry/Entity Type

Airline

Coding

Coded - Design and coding required

Number of Pages Required

5+ page

Font styles to use
Other font styles liked:
• Toronto subway font would be nice

Requirements
Must have
• A modern feel, easy to use, our booking function is currently a bit confusing which we will be working on. Content can be taken from our current website www.skymerrow-example.com
Nice to have
• work with out theme colours of blue and light grey

```html
<!DOCTYPE html>
<html lang="en">
<head>
<meta charset="utf-8">
<title>SkyMerrow — Home</title>
<link href="https://fonts.googleapis.com/css2?family=Open+Sans:wght@400;600&family=Raleway:wght@400;500;600;700&display=swap" rel="stylesheet">
<style>
:root{
  --navy:#003a8c;
  --nav-active:#061d5b;
  --nav-top:#9cc2ec;
  --nav-bottom:#5f96d6;
  --ink:#2b2b2b;
  --muted:#8a8a8a;
  --heading-blue:#0a2b6b;
  --link-blue:#2a5fb0;
  --panel-grey:#f1f1f1;
  --footer-grey:#eeeeee;
  --white:#ffffff;
}
*{margin:0;padding:0;box-sizing:border-box}
html,body{width:1200px;height:2778px;overflow:hidden;background:var(--white)}
body{position:relative;font-family:"Open Sans",Arial,sans-serif;color:var(--ink)}
.abs{position:absolute}

/* header */
.site-header{position:absolute;left:0;top:0;width:1200px;height:109px;background:var(--white)}
.brand{position:absolute;left:0;width:1200px;top:30px;display:flex;justify-content:center;align-items:center;gap:12px}
.brand-mark{width:40px;height:40px;border-radius:50%;background:#8a8f96}
.brand-name{font-family:"Raleway",sans-serif;font-weight:700;font-size:34px;color:#2f5fa8;letter-spacing:1px}

/* nav */
.main-nav{position:absolute;left:0;top:109px;width:1200px;height:52px;background:linear-gradient(var(--nav-top),var(--nav-bottom))}
.main-nav a{position:absolute;top:0;height:52px;line-height:52px;text-align:center;font-family:"Raleway",sans-serif;font-weight:700;font-size:15px;color:var(--white);text-decoration:none;border-right:1px solid rgba(255,255,255,.35)}
.main-nav a.active{background:var(--nav-active);border-right:none}

/* hero */
.hero{position:absolute;left:0;top:161px;width:1200px;height:513px;background:linear-gradient(160deg,#2a3550 0%,#4a5a78 40%,#6d7688 60%,#1f2a40 100%)}
.hero-title{position:absolute;left:0;width:1200px;top:180px;text-align:center;font-family:"Raleway",sans-serif;font-weight:700;font-size:37px;color:var(--white);letter-spacing:1px}
.hero-sub{position:absolute;left:0;width:1200px;top:230px;text-align:center;font-family:"Raleway",sans-serif;font-weight:700;font-size:29px;color:var(--white)}
.hero-btn{position:absolute;left:517px;top:298px;width:168px;height:41px;border:2px solid var(--white);color:var(--white);font-family:"Raleway",sans-serif;font-weight:700;font-size:14px;text-align:center;line-height:37px}
.hero-dots{position:absolute;left:560px;top:475px;display:flex;gap:8px}
.hero-dots span{width:14px;height:14px;border-radius:50%;border:2px solid var(--white)}
.hero-dots span.on{background:var(--white)}

/* welcome */
.welcome{position:absolute;left:0;top:674px;width:1200px;height:422px}
.welcome svg{position:absolute;left:0;top:0}
.welcome h1{position:absolute;left:0;width:1200px;top:68px;text-align:center;font-family:"Raleway",sans-serif;font-weight:500;font-size:34px;color:var(--white)}
.welcome p{position:absolute;text-align:center;font-size:16px;line-height:31px;color:#c9d6ee}
.welcome .lead{left:185px;width:830px;top:130px;font-size:16.5px}
.welcome .body{left:158px;width:884px;top:204px}

/* video */
.video-frame{position:absolute;left:124px;top:1165px;width:433px;height:272px;border:3px solid #d8d8d8;background:linear-gradient(180deg,#54646c 0%,#2f3d46 55%,#121a20 100%)}
.play{position:absolute;left:175px;top:95px;width:78px;height:78px;border:3px solid var(--white);border-radius:50%}
.play:after{content:"";position:absolute;left:28px;top:19px;border-left:26px solid var(--white);border-top:17px solid transparent;border-bottom:17px solid transparent}
.section-title{font-family:"Raleway",sans-serif;font-weight:500;font-size:28px;color:var(--heading-blue)}
.small-text{font-size:13px;line-height:20px;color:var(--muted)}
.btn-blue{position:absolute;width:123px;height:35px;background:linear-gradient(#7fb0e6,#4e86cf);color:var(--white);font-family:"Raleway",sans-serif;font-weight:700;font-size:11px;text-align:center;line-height:35px;border-radius:2px}

/* split */
.split{position:absolute;left:0;top:1511px;width:1200px;height:408px}
.split h2{position:absolute;font-family:"Raleway",sans-serif;font-weight:500;font-size:25px;color:var(--white)}
.split p{position:absolute;width:400px;font-size:13.5px;line-height:20px;color:var(--white)}
.btn-outline{position:absolute;width:122px;height:39px;border:2px solid var(--white);color:var(--white);font-family:"Raleway",sans-serif;font-weight:600;font-size:13px;text-align:center;line-height:35px}

/* gallery */
.gallery{position:absolute;left:0;top:1919px;width:1200px;height:357px;background:var(--panel-grey)}
.gallery h2{position:absolute;left:0;width:1200px;top:36px;text-align:center;font-family:"Raleway",sans-serif;font-weight:600;font-size:25px;color:#555}
.thumb{position:absolute;top:96px;width:222px;height:170px;border:3px solid var(--white);box-shadow:0 0 3px rgba(0,0,0,.25)}

/* news */
.news-title{position:absolute;left:124px;top:2333px;font-family:"Raleway",sans-serif;font-weight:500;font-size:24px;color:var(--heading-blue)}
.news-arrow{position:absolute;top:2335px;width:26px;height:26px;border-radius:50%;background:#e6e6e6;color:#999;font-size:14px;text-align:center;line-height:25px}
.news-item{position:absolute;top:2383px;width:290px}
.news-item h3{font-family:"Open Sans",sans-serif;font-weight:400;font-size:16px;color:var(--link-blue);margin-bottom:10px}
.news-item p{font-size:13px;line-height:21px;color:#666}
.news-item .age{margin-top:8px;font-size:12.5px;font-weight:600;color:#555}

/* footer */
.site-footer{position:absolute;left:0;top:2602px;width:1200px;height:176px;background:var(--footer-grey)}
.footer-nav{position:absolute;left:126px;top:38px;display:flex;gap:30px}
.footer-nav a{font-family:"Raleway",sans-serif;font-weight:600;font-size:15px;color:#555;text-decoration:none}
.copyright{position:absolute;left:126px;top:72px;font-size:14px;color:#888}
.social{position:absolute;left:126px;top:112px;display:flex;gap:6px}
.social span{width:30px;height:30px;border-radius:50%;border:1.5px solid #999}
.partner{position:absolute;font-family:"Raleway",sans-serif;font-size:32px}
.partner-one{left:858px;top:38px;font-weight:500;letter-spacing:3px;color:#1f3a68}
.partner-two{left:890px;top:92px;font-weight:700;color:#1f2b3a}
</style>
</head>
<body>

<header class="site-header">
  <div class="brand"><span class="brand-mark"></span><span class="brand-name">SKYMERROW</span></div>
</header>

<nav class="main-nav">
  <a class="active" style="left:126px;width:126px">HOME</a>
  <a style="left:252px;width:122px">FLIGHTS</a>
  <a style="left:374px;width:185px">CHARTER &amp; FLEET</a>
  <a style="left:559px;width:134px">PACKAGES</a>
  <a style="left:693px;width:126px">GALLERY</a>
  <a style="left:819px;width:81px">FAQ</a>
  <a style="left:900px;width:122px;border-right:none">CONTACT</a>
</nav>

<section class="hero" role="img" aria-label="Night photograph of downtown office towers and lit streets">
  <div class="hero-title">VIVAMUS PORTTITOR PURUS NISI</div>
  <div class="hero-sub">ELEIFEND LIBERO A TEMPUS</div>
  <div class="hero-btn">BOOK NOW</div>
  <div class="hero-dots"><span></span><span class="on"></span><span class="on"></span><span class="on"></span></div>
</section>

<section class="welcome">
  <svg width="1200" height="422" viewBox="0 0 1200 422"><polygon points="0,0 1200,0 1200,317 600,422 0,317" fill="#003a8c"/></svg>
  <h1>Welcome to Our Website</h1>
  <p class="lead">Aonsectetuer augue nisi quis lacus Ut ac mi quis lacus mollis aliquam Curabitur iaculis tempus eros Curabitur vel mi sit amet magna malesuada ultrices Ut nisi erat fermentum</p>
  <p class="body">vel congue id euismod in elit Fusce ultricies orci ac feugiat suscipit leo massa sodales velit et scelerisque mi tortor at ipsum cligula augue bibendum accumsan vestibulum ut commodo a mi Morbi ornare gravida elit Integer congue augue &nbsp;Curabitur vel mi sit amet magna malesuada ultrices</p>
</section>

<section class="video">
  <div class="video-frame" role="img" aria-label="Video still of a city skyline seen from an aircraft window"><span class="play"></span></div>
  <h2 class="section-title abs" style="left:592px;top:1175px">OUR VIDEO</h2>
  <p class="small-text abs" style="left:594px;top:1228px;width:450px">Donec dictum lectus non odio Cras a ante vitae enim iaculis aliquam Mauris nunc quam venenatis nec euismod sit amet</p>
  <p class="small-text abs" style="left:594px;top:1280px;width:460px">Morbi diam mauris viverra in gravida eu mattis in ante Morbi eget arcu Morbi porta libero id ullamcorper nonummy nibh ligula pulvinar metus eget consectetuer augue nisi quis lacus Ut ac mi quis lacus mollis aliquam Curabitur iaculis tempus eros Curabitur</p>
  <div class="btn-blue" style="left:594px;top:1391px">READ MORE</div>
</section>

<section class="split">
  <svg class="abs" style="left:0;top:0" width="1200" height="408" viewBox="0 0 1200 408">
    <defs>
      <linearGradient id="charterTone" x1="0" y1="0" x2="1" y2="1"><stop offset="0" stop-color="#3f6fc4"/><stop offset="1" stop-color="#1d4fa8"/></linearGradient>
      <linearGradient id="flightsTone" x1="0" y1="0" x2="1" y2="1"><stop offset="0" stop-color="#c9c9c9"/><stop offset="0.5" stop-color="#9a9a9a"/><stop offset="1" stop-color="#6f6f6f"/></linearGradient>
    </defs>
    <rect width="1200" height="408" fill="url(#flightsTone)" role="img" aria-label="Greyscale photograph of a passenger jet over a city"/>
    <polygon points="0,0 639,0 550,408 0,408" fill="url(#charterTone)" role="img" aria-label="Blue-toned photograph of a private jet in flight"/>
  </svg>
  <h2 style="left:131px;top:85px">PRIVATE CHARTER</h2>
  <p style="left:131px;top:130px">Donec dictum lectus non odio Cras a ante vitae enim iaculis aliquam Mauris nunc quam venenatis nec</p>
  <p style="left:131px;top:183px">Morbi diam mauris viverra in gravida eu mattis in ante Morbi eget arcu Morbi porta libero id ullamcorper nonummy nibh ligula pulvinar metus eget consectetuer augue nisi quis lacus Ut ac mi qu</p>
  <div class="btn-outline" style="left:135px;top:289px">READ MORE</div>
  <h2 style="left:682px;top:85px">FLIGHTS</h2>
  <p style="left:682px;top:130px">Donec dictum lectus non odio Cras a ante vitae enim iaculis aliquam Mauris nunc quam venenatis nec</p>
  <p style="left:682px;top:183px">Morbi diam mauris viverra in gravida eu mattis in ante Morbi eget arcu Morbi porta libero id ullamcorper nonummy nibh ligula pulvinar metus eget consectetuer augue nisi quis lacus Ut ac mi qu</p>
  <div class="btn-outline" style="left:686px;top:289px">READ MORE</div>
</section>

<section class="gallery">
  <h2>OUR GALLERY</h2>
  <div class="thumb" style="left:124px;background:linear-gradient(160deg,#5a5a5e,#c2702e 60%,#3a2a22)" role="img" aria-label="Aerial photograph of a city at sunset"></div>
  <div class="thumb" style="left:369px;background:linear-gradient(180deg,#8aa6c4,#4a6a8a 55%,#2d3a44)" role="img" aria-label="Photograph of a tall observation tower and waterfront skyline"></div>
  <div class="thumb" style="left:613px;background:linear-gradient(180deg,#d8782e,#8a3a1e 55%,#2a1a16)" role="img" aria-label="Photograph of a skyline under a fiery orange sky"></div>
  <div class="thumb" style="left:857px;background:linear-gradient(160deg,#1a2030,#4a6a9a 50%,#15202e)" role="img" aria-label="Photograph looking up at a glass office tower"></div>
</section>

<section class="news">
  <h2 class="news-title">NEWS FEED</h2>
  <div class="news-arrow" style="left:1002px">&#8249;</div>
  <div class="news-arrow" style="left:1035px">&#8250;</div>
  <article class="news-item" style="left:126px">
    <h3>Fusce ultricies feugiat suscipi</h3>
    <p>Morbi diam mauris viverra in gravida eu mattis in ante Morbi eget arcu Morbi porta libero id ullamcorper nonummy</p>
    <div class="age">2 DAYS AGO</div>
  </article>
  <article class="news-item" style="left:452px">
    <h3>Donec dictum lectus non</h3>
    <p>Morbi diam mauris viverra in gravida eu mattis in ante Morbi eget arcu Morbi porta libero id ullamcorper nonummy</p>
    <div class="age">2 DAYS AGO</div>
  </article>
  <article class="news-item" style="left:776px">
    <h3>Cras id elit Integer quis</h3>
    <p>Morbi diam mauris viverra in gravida eu mattis in ante Morbi eget arcu Morbi porta libero id ullamcorper nonummy</p>
    <div class="age">2 DAYS AGO</div>
  </article>
</section>

<footer class="site-footer">
  <nav class="footer-nav"><a>HOME</a><a>FLIGHTS</a><a>CHARTER &amp; FLEET</a><a>PACKAGES</a><a>GALLERY</a><a>CONTACT</a></nav>
  <div class="copyright">© 2017 Company Name &nbsp;All right reserved</div>
  <div class="social"><span></span><span></span><span></span><span></span></div>
  <div class="partner partner-one">QUENBROOK</div>
  <div class="partner partner-two">tavlo</div>
</footer>

</body>
</html>
```